Brindle Sky Port needs a new upscale business card design for our high end aircraft hangar complex

Brindle Sky Port (BSP) is a large, upscale jet hangar complex in the US housing expensive aircraft. We need a new business card design, using our current logo. We will be attending a industry convention and need a card design that will stand out and be remembered by aircraft owners and private pilots.

Target Market(s)

Aircraft pilots or owners looking for a new upscale hangar

Industry/Entity Type

Airport

Contact Information for Business Card

I like to use very heavy card stock, 400#, double sided. Square, no rounded edges please.

Colors
3276b5
0255a3
85abd2

Requirements
Must have
• An expensive, classy design, vivid colors.
Nice to have
• Needs to look very expensive and classy, and have some "pop". Designer must be able to download or copy my current typeface or fonts.
• One card side might be black with the "Logo and Brindle Sky Port Double line image in blue (or try gold, or glossy black), and perhaps have a grayed out "K720 jet silhouette". The other card side would have our contact info, and perhaps the "BSP Logo only". I'd like my contact info 'stacked', not in a paragraph format.
Should not have
• Should not look "too busy". Having a double-sided card will help.

```html
<!DOCTYPE html>
<html lang="en">
<head>
<meta charset="utf-8">
<title>Brindle Sky Port — Business Card</title>
<link rel="stylesheet" href="https://fonts.googleapis.com/css2?family=Source+Sans+3:wght@400;600;700&display=swap">
<style>
  :root {
    --stage: #151515;
    --paper: #ffffff;
    --ink: #333333;
    --brand-blue: #1f6eaa;
    --navy: #0f4f86;
    --navy-deep: #0c4275;
    --face-top: #1a88c4;
    --face-bottom: #0f6aa5;
    --white: #ffffff;
  }
  * { margin: 0; padding: 0; box-sizing: border-box; }
  html, body {
    width: 1200px;
    height: 900px;
    overflow: hidden;
    background: var(--stage);
    font-family: "Source Sans 3", "Helvetica Neue", Arial, sans-serif;
  }
  .canvas {
    position: relative;
    width: 1200px;
    height: 900px;
  }
  .card {
    position: absolute;
    top: 306px;
    width: 438px;
    height: 270px;
    border-radius: 0;
    overflow: hidden;
  }
  .card--front {
    left: 150px;
    background: var(--paper);
  }
  .card--back {
    left: 609px;
    background: linear-gradient(180deg, var(--face-top), var(--face-bottom));
    display: flex;
    align-items: center;
    justify-content: center;
  }
  .card__accent {
    position: absolute;
    inset: 0;
    width: 438px;
    height: 270px;
  }
  .contact {
    position: absolute;
    left: 30px;
    top: 27px;
    color: var(--ink);
  }
  .contact__name {
    font-size: 17px;
    font-weight: 600;
    color: var(--brand-blue);
    line-height: 20px;
  }
  .contact__title {
    font-size: 13px;
    line-height: 16px;
  }
  .contact__address {
    margin-top: 26px;
    font-size: 13px;
    line-height: 16px;
  }
  .contact__list {
    list-style: none;
    margin-top: 11px;
    font-size: 13px;
  }
  .contact__item {
    display: flex;
    align-items: center;
    gap: 7px;
    height: 18px;
  }
  .contact__icon {
    width: 10px;
    height: 10px;
    fill: var(--brand-blue);
    flex: none;
  }
  .brand {
    display: flex;
    align-items: center;
    gap: 10px;
    margin-top: 40px;
  }
  .brand__mark {
    width: 14px;
    height: 14px;
    background: var(--white);
  }
  .brand__name {
    font-size: 26px;
    font-weight: 700;
    color: var(--white);
    letter-spacing: 0.3px;
  }
</style>
</head>
<body>
<main class="canvas">
  <section class="card card--front" aria-label="Business card front">
    <svg class="card__accent" viewBox="0 0 438 270" role="img" aria-label="Navy accent area with the brand's diagonal graphic">
      <defs>
        <linearGradient id="accentFill" x1="0" y1="0" x2="1" y2="1">
          <stop offset="0" stop-color="var(--navy)"/>
          <stop offset="1" stop-color="var(--navy-deep)"/>
        </linearGradient>
      </defs>
      <polygon points="130,270 438,0 438,270" fill="url(#accentFill)"/>
    </svg>
    <div class="contact">
      <p class="contact__name">Marcus Hale</p>
      <p class="contact__title">Managing Director</p>
      <p class="contact__address">12345, Address Goes Here<br>Country Name, 123456.</p>
      <ul class="contact__list">
        <li class="contact__item">
          <svg class="contact__icon" viewBox="0 0 10 10"><path d="M2,0.5 L4,2.5 L3,3.8 C3.8,5.3 4.7,6.2 6.2,7 L7.5,6 L9.5,8 L8,9.5 C4,9 1,6 0.5,2 Z"/></svg>
          (044)-456-7890
        </li>
        <li class="contact__item">
          <svg class="contact__icon" viewBox="0 0 10 10"><path d="M2,0 H7 V3 H9 V9 H1 V3 H2 Z M3,1 V3 H6 V1 Z M3,5 V6 H7 V5 Z"/></svg>
          123-456-7890
        </li>
        <li class="contact__item">
          <svg class="contact__icon" viewBox="0 0 10 10"><path d="M0,2 H10 V8 H0 Z M0.8,2.6 L5,5.6 L9.2,2.6" stroke="#fff" stroke-width="0.8"/></svg>
          info@youremail.com
        </li>
        <li class="contact__item">
          <svg class="contact__icon" viewBox="0 0 10 10"><circle cx="5" cy="5" r="4.5"/></svg>
          www.website.com
        </li>
      </ul>
    </div>
  </section>

  <section class="card card--back" aria-label="Business card back">
    <div class="brand">
      <span class="brand__mark"></span>
      <span class="brand__name">Brindle Sky Port</span>
    </div>
  </section>
</main>
</body>
</html>
```